Clean Modern Skin Product branding/ label.

I need a label for a skincare line. The company is Dermaloft but product names will vary. A couple products to list are:
Sensitive Cleanser, Lumeno, Repair, Halo up, Mendora, Mendora Plus, Mendora Intense, Tavelo, Balance and Vivanto.

I would like the color scheme to be muted greens, grays, tourquise. The bottles are white, boston shaped with pumps, and ounces are 2, 4, 8, 16 ounces. When I choose the design, I can give you exact label sizes. Along with the ingredience already on the product label.

The look I desire is clean, minimal. A modern, organic look. Ideas that come to mind are a Veloraine,https://www.veloraine-example.com/product/2846/37204/3-step/step-2-exfoliate/clarifying-lotion-1 and the simplicity of Bo Tarn.

Both styles high light the name, in this case Dermaloft, and then the specific product.

My product is clean utilizing pure ingredients rather that a bunch fillers and binders. When I work with my clients I normally will say we need to "restore the balance" from over use of harsh products. That is why this lines works. It restores the skin to it's natural state. The process is simple, so I would like the label to reflect that simplicity.

Target Market(s)

Anyone with sensitive skin. So gender neutral

Industry/Entity Type

Skin Care Product

Font styles to use
Serif
Sans Serif
Decorative

Colors
acd037
33b8a4
fcfefd
85cae6
d3d3d3

Requirements
Must have
• Logo, name of product and color identity for cleanser, Active products, moisturizers
• I am thinking we could have one color for a cleanser and a space where I can put a sticker on which cleanser it is. Acne Cleasner, Sensitive Cleanser, and Cleanser.
Nice to have
• Not sure....suprise me. I would like the font to stay the same on the DERMALOFT, but you can change color, or color of leaf.
Should not have
• Too busy, too crowded or look like every other skincare line

```html
<!DOCTYPE html>
<html lang="en">
<head>
<meta charset="utf-8">
<title>Dermaloft – Sensitive Cleanser Label</title>
<link rel="stylesheet" href="https://fonts.googleapis.com/css2?family=Roboto:wght@300;400;700&display=swap">
<style>
  :root {
    --backdrop: #4f9798;
    --label-white: #ffffff;
    --brand-gray: #55595d;
    --product-teal: #3f7f8f;
    --rule-teal: #3f7f8f;
    --leaf-green: #7be41c;
    --leaf-deep: #3f9a16;
    --tagline-green: #84ea1e;
  }
  html, body {
    margin: 0;
    padding: 0;
    width: 1200px;
    height: 1200px;
    overflow: hidden;
    background: var(--backdrop);
  }
  .canvas {
    position: relative;
    width: 1200px;
    height: 1200px;
  }
  .label {
    position: absolute;
    left: 170px;
    top: 95px;
    width: 860px;
    height: 1010px;
    background: var(--label-white);
    box-shadow: 0 4px 18px rgba(0,0,0,0.12);
  }
  .brand-name {
    position: absolute;
    left: 0;
    right: 0;
    top: 128px;
    margin: 0;
    text-align: center;
    font-family: "Roboto", sans-serif;
    font-weight: 400;
    font-size: 100px;
    line-height: 1;
    letter-spacing: -1px;
    color: var(--brand-gray);
  }
  .product-name {
    position: absolute;
    left: 193px;
    top: 327px;
    width: 474px;
    height: 65px;
    margin: 0;
    border-top: 1.5px solid var(--rule-teal);
    border-bottom: 1.5px solid var(--rule-teal);
    text-align: center;
    font-family: "Roboto", sans-serif;
    font-weight: 300;
    font-size: 54px;
    line-height: 65px;
    color: var(--product-teal);
  }
  .leaf-art {
    position: absolute;
    left: 365px;
    top: 711px;
    width: 131px;
    height: 138px;
  }
  .tagline {
    position: absolute;
    left: 0;
    right: 0;
    top: 852px;
    margin: 0;
    text-align: center;
    font-family: "Roboto", sans-serif;
    font-weight: 700;
    font-size: 37px;
    line-height: 1.1;
    color: var(--tagline-green);
  }
</style>
</head>
<body>
  <div class="canvas">
    <section class="label">
      <h1 class="brand-name">Dermaloft</h1>
      <h2 class="product-name">Sensitive Cleanser</h2>
      <svg class="leaf-art" role="img" aria-label="Green leaf illustration" viewBox="0 0 131 138">
        <defs>
          <linearGradient id="leafTone" x1="0" y1="1" x2="1" y2="0">
            <stop offset="0" stop-color="var(--leaf-deep)"/>
            <stop offset="1" stop-color="var(--leaf-green)"/>
          </linearGradient>
        </defs>
        <rect x="0" y="0" width="131" height="138" rx="10" fill="url(#leafTone)"/>
      </svg>
      <p class="tagline">restore the balance</p>
    </section>
  </div>
</body>
</html>
```